New Innovative Counselling and psychotherapy Service needs Business Card design

Keep it simple and professional. On one side, just company name and logo (perhaps in all blue) and maybe a tag line.

On other side (all white) my name and Qualifications in centre

Industry/Entity Type

Health And Wellness

Contact Information for Business Card

Dara Whelby
Counsellor & Psychotherapist
BSc (Psychol.), BA, Dip. (Couns. & Psych.), PG.Cert (CBT), FGTrK, ONRE

I will also require Mobile no, Email and web site address of which I'll pass on to final designer.

Font styles to use
Sans Serif

Requirements
Must have
• My Logo Only and please use the colours in logo that is in it.
Should not have
• Any other images

```html
<!DOCTYPE html>
<html lang="en">
<head>
<meta charset="utf-8">
<title>Kindred Lane – Business Card</title>
<link rel="stylesheet" href="https://fonts.googleapis.com/css2?family=PT+Sans:wght@400;700&display=swap">
<style>
  :root {
    --backdrop: #3b3431;
    --card: #151618;
    --brand-blue: #3d8fbd;
    --brand-green: #7ab648;
    --text-light: #e9ecef;
    --text-muted: #8a8d91;
    --rule: #5a5d61;
  }
  * { box-sizing: border-box; margin: 0; padding: 0; }
  html, body {
    width: 1200px; height: 864px; overflow: hidden;
    background: var(--backdrop);
    font-family: "PT Sans", sans-serif;
  }
  .sheet {
    width: 1200px; height: 864px;
    display: flex; align-items: center; justify-content: center; gap: 40px;
  }
  .card {
    width: 540px; height: 309px;
    background: var(--card);
    position: relative;
    box-shadow: 0 10px 24px rgba(0,0,0,.45);
  }
  /* Front */
  .card-front .brand {
    position: absolute; top: 92px; left: 0; right: 0;
    display: flex; align-items: center; justify-content: center; gap: 14px;
  }
  .brand-dot {
    width: 40px; height: 40px; border-radius: 50%;
    background: var(--brand-blue);
  }
  .card-front .brand-name {
    font-size: 38px; font-weight: 400; color: var(--brand-blue);
  }
  .tagline {
    position: absolute; top: 196px; left: 0; right: 0;
    text-align: center; font-size: 15px; font-style: italic;
    color: var(--text-muted);
  }
  /* Back */
  .identity { position: absolute; left: 34px; top: 58px; }
  .person-name {
    font-size: 21px; font-weight: 700; color: var(--brand-blue);
    text-transform: uppercase; letter-spacing: .3px;
  }
  .person-role {
    font-size: 15px; color: var(--brand-green);
    text-transform: uppercase; margin-top: 2px;
  }
  .credentials {
    font-size: 11.5px; color: var(--brand-green);
    line-height: 1.35; margin-top: 3px;
  }
  .divider {
    width: 200px; height: 1px; background: var(--rule); margin: 12px 0 12px;
  }
  .contact-list { list-style: none; }
  .contact-list li {
    display: flex; align-items: center; gap: 9px;
    font-size: 13.5px; color: var(--text-light); line-height: 1.55;
  }
  .contact-list svg { width: 12px; height: 12px; flex: none; }
  .card-back .brand {
    position: absolute; right: 34px; top: 88px;
    display: flex; align-items: center; gap: 10px;
  }
  .card-back .brand-dot { width: 26px; height: 26px; }
  .card-back .brand-name { font-size: 25px; color: var(--text-light); }
  .base-rule {
    position: absolute; left: 34px; right: 34px; bottom: 42px;
    height: 1px; background: var(--rule);
  }
</style>
</head>
<body>
<main class="sheet">
  <section class="card card-front" aria-label="Card front">
    <div class="brand">
      <span class="brand-dot"></span>
      <span class="brand-name">Kindred Lane</span>
    </div>
    <p class="tagline">Caring For Your Psychological Well-Being Is Our Top Priority</p>
  </section>

  <section class="card card-back" aria-label="Card back">
    <div class="identity">
      <h1 class="person-name">Dara Whelby</h1>
      <p class="person-role">Counsellor &amp; Psychotherapist</p>
      <p class="credentials">BSc (Psychol.), BA, Dip. (Couns. &amp; Psych.)<br>PG.Cert (CBT), FGTrK.</p>
      <div class="divider"></div>
      <ul class="contact-list">
        <li>
          <svg viewBox="0 0 12 12" aria-hidden="true"><rect x="3" y="0.5" width="6" height="11" rx="1" fill="none" stroke="var(--brand-blue)" stroke-width="1.2"/><circle cx="6" cy="9.6" r=".7" fill="var(--brand-blue)"/></svg>
          555 014 2738
        </li>
        <li>
          <svg viewBox="0 0 12 12" aria-hidden="true"><rect x="0.5" y="2" width="11" height="8" fill="var(--brand-blue)"/><path d="M0.5 2 L6 6.5 L11.5 2" fill="none" stroke="var(--card)" stroke-width="1"/></svg>
          dara@kindredlane.com
        </li>
        <li>
          <svg viewBox="0 0 12 12" aria-hidden="true"><circle cx="6" cy="6" r="5.5" fill="var(--brand-blue)"/><path d="M0.5 6 H11.5 M6 0.5 C3 3.5 3 8.5 6 11.5 M6 0.5 C9 3.5 9 8.5 6 11.5" fill="none" stroke="var(--card)" stroke-width=".8"/></svg>
          www.kindredlane.com
        </li>
      </ul>
    </div>
    <div class="brand">
      <span class="brand-dot"></span>
      <span class="brand-name">Kindred Lane</span>
    </div>
    <div class="base-rule"></div>
  </section>
</main>
</body>
</html>
```